Harborline Auto LLC

Car Dealer Customer Service
Address: 2874 Cresthaven Road, Shelbyville, TN 37162
web: www.harborlineautoxq.net
email: harborlineautoxq@mailnest.example
Phone: (931) 555-0148
Phone: (629) 555-0173

```html
<!DOCTYPE html>
<html lang="en">
<head>
<meta charset="utf-8">
<title>Harborline Auto – Business Card</title>
<link href="https://fonts.googleapis.com/css2?family=Montserrat:wght@400;500;800&display=swap" rel="stylesheet">
<style>
  :root {
    --page-bg: #d6d6d6;
    --brand-blue: #2590c8;
    --brand-blue-deep: #1b78ad;
    --brand-gold: #e9b040;
    --card-white: #ffffff;
    --text-light: #ffffff;
  }
  * { box-sizing: border-box; margin: 0; padding: 0; }
  html, body { width: 1200px; height: 813px; overflow: hidden; }
  body {
    background: var(--page-bg);
    font-family: "Montserrat", Arial, sans-serif;
    position: relative;
  }
  .card {
    position: absolute;
    left: 280px;
    width: 640px;
    height: 366px;
    border-radius: 22px;
    overflow: hidden;
    box-shadow: 0 6px 18px rgba(0,0,0,0.25);
  }
  .card--front { top: 30px; background: var(--card-white); }
  .card--back {
    top: 417px;
    background: linear-gradient(135deg, var(--brand-blue) 0%, var(--brand-blue-deep) 100%);
  }
  .card__wave { position: absolute; inset: 0; }

  .brand { position: absolute; display: flex; flex-direction: column; align-items: center; }
  .brand__name { font-weight: 800; letter-spacing: 0.04em; text-transform: uppercase; white-space: nowrap; }
  .brand--front { left: 30px; top: 70px; }
  .brand--front .brand__dot { width: 76px; height: 76px; border-radius: 50%; background: var(--brand-blue); margin-bottom: 14px; }
  .brand--front .brand__name { color: var(--brand-blue-deep); font-size: 21px; }

  .brand--back { left: 0; right: 0; top: 74px; }
  .brand--back .brand__dot { width: 130px; height: 130px; border-radius: 50%; background: var(--text-light); margin-bottom: 24px; }
  .brand--back .brand__name { color: var(--text-light); font-size: 46px; }

  .contact {
    position: absolute;
    right: 22px;
    top: 40px;
    color: var(--text-light);
    font-size: 12.5px;
    font-weight: 500;
    text-align: right;
    line-height: 22px;
  }
  .contact__group { margin-bottom: 14px; }
  .contact__line { display: flex; justify-content: flex-end; align-items: center; gap: 8px; white-space: nowrap; }
  .contact__icon { width: 13px; height: 13px; flex: none; }
</style>
</head>
<body>

<section class="card card--front">
  <svg class="card__wave" viewBox="0 0 640 366" aria-hidden="true">
    <path d="M440 0 C340 40 340 170 250 260 C180 330 90 360 0 352 L0 366 L640 366 L640 0 Z" fill="var(--brand-blue)"/>
    <path d="M425 -2 C325 40 325 165 235 252 C165 322 80 348 0 340" fill="none" stroke="var(--brand-gold)" stroke-width="9"/>
    <path d="M408 -2 C310 38 308 158 220 244 C152 312 72 336 0 328" fill="none" stroke="var(--brand-blue)" stroke-width="3"/>
  </svg>

  <div class="brand brand--front">
    <span class="brand__dot"></span>
    <span class="brand__name">Harborline Auto</span>
  </div>

  <div class="contact">
    <div class="contact__group">
      <div class="contact__line">Car Dealer Customer Service</div>
      <div class="contact__line">2874 Cresthaven Road</div>
      <div class="contact__line">Shelbyville, TN 37162</div>
    </div>
    <div class="contact__group">
      <div class="contact__line">(931) 555-0148
        <svg class="contact__icon" viewBox="0 0 16 16" aria-hidden="true"><path d="M3 1h3l1.5 4-2 1.2a9 9 0 0 0 4.3 4.3L11 8.5l4 1.5v3a2 2 0 0 1-2 2A12 12 0 0 1 1 3a2 2 0 0 1 2-2z" fill="#fff"/></svg>
      </div>
      <div class="contact__line">(629) 555-0173
        <svg class="contact__icon" viewBox="0 0 16 16" aria-hidden="true"><rect x="4" y="1" width="8" height="14" rx="1.5" fill="#fff"/><rect x="5.5" y="3" width="5" height="8" fill="var(--brand-blue)"/></svg>
      </div>
    </div>
    <div class="contact__group">
      <div class="contact__line">harborlineautoxq@mailnest.example
        <svg class="contact__icon" viewBox="0 0 16 16" aria-hidden="true"><rect x="1" y="3" width="14" height="10" rx="1" fill="#fff"/><path d="M1.5 4 8 9l6.5-5" fill="none" stroke="var(--brand-blue)" stroke-width="1.3"/></svg>
      </div>
      <div class="contact__line">www.harborlineautoxq.net
        <svg class="contact__icon" viewBox="0 0 16 16" aria-hidden="true"><circle cx="8" cy="8" r="7" fill="#fff"/><path d="M1 8h14M8 1c-3 3-3 11 0 14M8 1c3 3 3 11 0 14" fill="none" stroke="var(--brand-blue)" stroke-width="1"/></svg>
      </div>
    </div>
  </div>
</section>

<section class="card card--back">
  <div class="brand brand--back">
    <span class="brand__dot"></span>
    <span class="brand__name">Harborline Auto</span>
  </div>
</section>

</body>
</html>
```